BOLD & MINIMALIST DESIGN NEEDED

We want a very bold but minimalistic business card design that is impactful and utilizes both sides of the business card. Our current logo is included for your use.

We want bold fonts and good use of negative space. We don't want the logo to overpower the design.

Target Market(s)

Professionals who are building new commercial buildings.

Industry/Entity Type

Construction

Contact Information for Business Card

Name, Title, email, office phone, cell phone, website

Font styles to use
Serif
Sans Serif

Requirements
Must have
• Bold design!

```html
<!DOCTYPE html>
<html lang="en">
<head>
<meta charset="utf-8">
<title>Ridgeline – Business Card</title>
<link rel="stylesheet" href="https://fonts.googleapis.com/css2?family=Arimo:wght@400;700&display=swap">
<style>
  :root {
    --green: #8cc63f;
    --green-light: #b5dc7a;
    --black: #0d0d0d;
    --ink: #111111;
    --grey-text: #555555;
    --paper: #ffffff;
    --backdrop: #e4e4e4;
  }
  * { margin: 0; padding: 0; box-sizing: border-box; }
  html, body {
    width: 1200px;
    height: 1200px;
    overflow: hidden;
    background: var(--backdrop);
    font-family: "Arimo", Arial, sans-serif;
  }
  .card {
    position: absolute;
    left: 255px;
    width: 690px;
    height: 394px;
    overflow: hidden;
  }
  /* Front */
  .card-front {
    top: 158px;
    background: var(--paper);
  }
  .brand {
    position: absolute;
    left: 0;
    width: 362px;
    top: 0;
    height: 370px;
    display: flex;
    align-items: center;
    justify-content: center;
    gap: 10px;
  }
  .brand-mark {
    width: 18px;
    height: 18px;
    background: var(--green);
  }
  .brand-name {
    font-weight: 700;
    font-size: 34px;
    letter-spacing: 1px;
    color: var(--ink);
  }
  .divider {
    position: absolute;
    left: 362px;
    top: 115px;
    width: 1px;
    height: 170px;
    background: #cfcfcf;
  }
  .person {
    position: absolute;
    left: 385px;
    top: 118px;
  }
  .person-name {
    font-weight: 700;
    font-size: 27px;
    color: var(--ink);
    letter-spacing: 0.3px;
    line-height: 1;
  }
  .person-title {
    font-size: 15px;
    color: var(--green);
    margin-top: 6px;
  }
  .contacts {
    list-style: none;
    position: absolute;
    left: 384px;
    top: 187px;
  }
  .contacts li {
    display: flex;
    align-items: center;
    height: 20.5px;
    font-size: 16px;
    color: var(--grey-text);
  }
  .contacts svg {
    width: 14px;
    height: 14px;
    margin-right: 12px;
    fill: var(--ink);
    flex: none;
  }
  .rule-green {
    position: absolute;
    left: 0; right: 0;
    top: 371px;
    height: 3px;
    background: var(--green);
  }
  .band-black {
    position: absolute;
    left: 0; right: 0;
    top: 376px;
    bottom: 0;
    background: var(--black);
  }
  /* Back */
  .card-back {
    top: 652px;
    background: radial-gradient(ellipse 55% 60% at 50% 42%, var(--green-light) 0%, var(--green) 100%);
    display: flex;
    align-items: center;
    justify-content: center;
    gap: 18px;
  }
  .card-back .brand-mark {
    width: 30px;
    height: 30px;
    background: var(--black);
  }
  .card-back .brand-name {
    font-size: 66px;
    letter-spacing: 2px;
  }
</style>
</head>
<body>
  <section class="card card-front">
    <div class="brand">
      <span class="brand-mark"></span>
      <span class="brand-name">RIDGELINE</span>
    </div>
    <div class="divider"></div>
    <div class="person">
      <div class="person-name">DANIEL REYES</div>
      <div class="person-title">President</div>
    </div>
    <ul class="contacts">
      <li>
        <svg viewBox="0 0 16 16" aria-hidden="true"><path d="M3.5 1l2.5 3-1.5 2c1 2 3 4 5 5l2-1.5 3 2.5-1.5 2.5C8 16 0 8 1 2.5z"/></svg>
        555-213-4870
      </li>
      <li>
        <svg viewBox="0 0 16 16" aria-hidden="true"><path d="M4 0h8v16H4zM5.5 2v10h5V2zM7 13h2v1.5H7z" fill-rule="evenodd"/></svg>
        555-219-6042
      </li>
      <li>
        <svg viewBox="0 0 16 16" aria-hidden="true"><path d="M1 4h14v9H1zM2.5 5.5v.3L8 9.5l5.5-3.7v-.3zM2.5 7.6v3.9h11V7.6L8 11.3z" fill-rule="evenodd"/></svg>
        info@ridgelinebuild.com
      </li>
      <li>
        <svg viewBox="0 0 16 16" aria-hidden="true"><circle cx="8" cy="8" r="7"/><path d="M5 4c2 0 2 2 4 2s1 3-1 3-1 3-3 2-1-3-2-4 0-3 2-3z" fill="#fff"/></svg>
        www.ridgelinebuild.com
      </li>
    </ul>
    <div class="rule-green"></div>
    <div class="band-black"></div>
  </section>

  <section class="card card-back">
    <span class="brand-mark"></span>
    <span class="brand-name">RIDGELINE</span>
  </section>
</body>
</html>
```